professional business card design for technology company

We are a small technology consulting firm, specialising in consulting based around Cloud and Managed services. Our colour scheme is yellow, blue and white, as you can see in the logos. Although we are based in melbourne australia, due to the nature of our work, our clients can be located anywhere. We are looking for a clean, professional, positive look - similar to our company logo

Target Market(s)

small business

Industry/Entity Type

Business

Contact Information for Business Card

eye catching, designed to incorporate some level of raised printing. Must contain website address, phone number, name and job title

Requirements
Must have
• Logo (attached) - use of the same colour scheme

```html
<!DOCTYPE html>
<html lang="en">
<head>
<meta charset="utf-8">
<title>Nubora Business Card</title>
<link rel="stylesheet" href="https://fonts.googleapis.com/css2?family=Montserrat:wght@300;400;700&family=Open+Sans:wght@400;600&display=swap">
<style>
  :root {
    --page: #d9d6d2;
    --card-light: #f0f0f0;
    --card-dark: #2a2a2b;
    --brand-blue: #2ea6dc;
    --brand-yellow: #f2cf1d;
    --ink-grey: #555556;
    --ink-white: #ffffff;
    --ink-muted: #4a4a4a;
  }
  * { box-sizing: border-box; margin: 0; padding: 0; }
  html, body { width: 1200px; height: 960px; overflow: hidden; }
  body {
    background: var(--page);
    font-family: "Open Sans", sans-serif;
    position: relative;
  }
  .card {
    position: absolute;
    left: 220px;
    width: 760px;
    height: 420px;
    background: var(--card-light);
    overflow: hidden;
    box-shadow: 0 6px 18px rgba(0,0,0,0.18);
  }
  .card--back { top: 45px; }
  .card--front { top: 495px; display: flex; }

  .brand {
    display: flex;
    align-items: center;
    gap: 18px;
  }
  .brand__dot {
    width: 46px; height: 46px;
    border-radius: 50%;
    background: var(--brand-blue);
  }
  .brand__name {
    font-family: "Montserrat", sans-serif;
    font-weight: 700;
    color: var(--ink-grey);
    letter-spacing: -1px;
    line-height: 1;
  }

  .card--back .brand {
    position: absolute;
    left: 0; right: 0; top: 130px;
    justify-content: center;
  }
  .card--back .brand__name { font-size: 92px; }
  .card--back .brand__dot { width: 60px; height: 60px; }
  .back-band {
    position: absolute;
    left: 0; right: 0; bottom: 0;
    height: 90px;
    background: var(--card-dark);
    display: flex;
    align-items: center;
    justify-content: center;
  }
  .back-band__url {
    color: var(--ink-white);
    font-size: 15px;
    letter-spacing: 4px;
  }

  .front-info {
    width: 430px;
    height: 100%;
    background: var(--card-dark);
    position: relative;
  }
  .name-band {
    position: absolute;
    left: 0; right: 0; top: 60px;
    height: 78px;
    background: var(--brand-blue);
    padding: 14px 0 0 70px;
    font-family: "Montserrat", sans-serif;
  }
  .name-band__name {
    font-size: 24px;
    color: var(--ink-white);
    letter-spacing: 0.5px;
  }
  .name-band__given { font-weight: 700; }
  .name-band__family { font-weight: 300; color: var(--ink-muted); }
  .name-band__title {
    font-size: 14px;
    font-weight: 300;
    color: var(--ink-muted);
    margin-top: 2px;
  }
  .contacts {
    position: absolute;
    left: 70px; top: 200px;
    list-style: none;
  }
  .contacts__item {
    display: flex;
    align-items: center;
    gap: 18px;
    color: var(--ink-white);
    font-size: 15px;
    margin-bottom: 20px;
  }
  .contacts__icon {
    width: 34px; height: 34px;
    border-radius: 6px;
    background: var(--brand-blue);
    display: flex;
    align-items: center;
    justify-content: center;
  }
  .front-logo {
    flex: 1;
    display: flex;
    align-items: center;
    justify-content: center;
  }
  .front-logo .brand__name { font-size: 58px; }
  .front-logo .brand__dot { width: 40px; height: 40px; }
</style>
</head>
<body>
  <section class="card card--back" aria-label="Card back">
    <div class="brand">
      <span class="brand__dot"></span>
      <span class="brand__name">Nubora</span>
    </div>
    <div class="back-band">
      <span class="back-band__url">www.nubora.com</span>
    </div>
  </section>

  <section class="card card--front" aria-label="Card front">
    <div class="front-info">
      <div class="name-band">
        <p class="name-band__name"><span class="name-band__given">MARLO T.</span> <span class="name-band__family">VANCE</span></p>
        <p class="name-band__title">PRINCIPAL</p>
      </div>
      <ul class="contacts">
        <li class="contacts__item">
          <span class="contacts__icon">
            <svg width="18" height="18" viewBox="0 0 24 24"><path fill="#2a2a2b" d="M6.6 10.8a15.1 15.1 0 0 0 6.6 6.6l2.2-2.2c.3-.3.7-.4 1-.2 1.1.4 2.3.6 3.6.6.6 0 1 .4 1 1V20c0 .6-.4 1-1 1A17 17 0 0 1 3 4c0-.6.4-1 1-1h3.5c.6 0 1 .4 1 1 0 1.3.2 2.5.6 3.6.1.3 0 .7-.2 1z"/></svg>
          </span>
          555-014-2738
        </li>
        <li class="contacts__item">
          <span class="contacts__icon">
            <svg width="18" height="18" viewBox="0 0 24 24"><path fill="#2a2a2b" d="M3 5h18v14H3z"/><path fill="none" stroke="#2ea6dc" stroke-width="1.8" d="M3 5l9 8 9-8"/></svg>
          </span>
          MarloTVance@nubora.com
        </li>
        <li class="contacts__item">
          <span class="contacts__icon">
            <svg width="18" height="18" viewBox="0 0 24 24"><circle cx="12" cy="12" r="9" fill="#2a2a2b"/><path fill="none" stroke="#2ea6dc" stroke-width="1.4" d="M3 12h18M12 3c3 3 3 15 0 18M12 3c-3 3-3 15 0 18"/></svg>
          </span>
          www.nubora.com
        </li>
      </ul>
    </div>
    <div class="front-logo">
      <div class="brand">
        <span class="brand__dot"></span>
        <span class="brand__name">Nubora</span>
      </div>
    </div>
  </section>
</body>
</html>
```